need corporate, modern business card created for Consulting Company

I need a slick business card using elements from my website, as well as, integrating my pixelforge-created logo (see files).

The business card needs to be:
1. Corporate and modern
2. Clean and professional

I've included a PSD with the logo/icon that you can use to create it. Feel free to try a metallic finish on the logo, make it bigger/small, underlay it. Whatever you need to do to make my card stand out.

Try a black background, or white background or gray.

The idea is for my card to be memorable as well as professional and corporate.

Target Market(s)

Corporate business in the US and Canada.

Industry/Entity Type

Business

Contact Information for Business Card

Commerce Advancing Methods
Martin Coles, Senior Partner
office: 1 877 555 0143
mobile: 1 519 555 0172
website: http://www.brightvale.example

Requirements
Must have
• Card-related information
• corporate, yet modern
• clean and professional
• incorporate the icon only
• must have an editable form when complete!
Nice to have
• metallic icon might be cool
• try it with white or black

```html
<!DOCTYPE html>
<html lang="en">
<head>
<meta charset="utf-8">
<title>Brightvale Business Card</title>
<link rel="stylesheet" href="https://fonts.googleapis.com/css2?family=Exo+2:wght@400;500;600&display=swap">
<style>
  :root {
    --page-bg: #d9d9db;
    --card-black: #1f1f21;
    --brand-blue: #2f6bc4;
    --swoosh-gray: #a9abae;
    --text-white: #ffffff;
    --text-soft: #e4e4e6;
  }
  * { margin: 0; padding: 0; box-sizing: border-box; }
  html, body {
    width: 1200px; height: 899px; overflow: hidden;
    background: var(--page-bg);
    font-family: "Exo 2", sans-serif;
  }
  .sheet {
    width: 1200px; height: 899px;
    display: flex; flex-direction: column; align-items: center; justify-content: center;
    gap: 40px;
  }
  .card {
    position: relative;
    width: 700px; height: 400px;
    border-radius: 38px;
    overflow: hidden;
    background: var(--card-black);
    box-shadow: 0 6px 18px rgba(0,0,0,0.25);
  }
  .card-waves { position: absolute; inset: 0; }
  .holder { position: absolute; right: 52px; top: 42px; text-align: right; color: var(--text-white); }
  .holder-name { font-size: 28px; font-weight: 500; letter-spacing: 2px; text-transform: uppercase; }
  .holder-role { font-size: 19px; font-weight: 400; margin-top: 4px; }
  .brand {
    position: absolute; display: flex; align-items: center; gap: 12px;
    color: var(--brand-blue); font-weight: 600; letter-spacing: 0.5px;
    white-space: nowrap;
  }
  .brand-mark { background: var(--brand-blue); display: block; }
  .front .brand { left: 340px; top: 214px; font-size: 54px; }
  .front .brand-mark { width: 26px; height: 26px; }
  .contacts {
    position: absolute; left: 36px; top: 222px;
    list-style: none; color: var(--text-soft); font-size: 13px;
  }
  .contacts li { display: flex; align-items: center; gap: 9px; height: 23px; white-space: nowrap; }
  .contacts svg { width: 13px; height: 13px; fill: var(--text-soft); flex: none; }
  .contacts .globe { fill: none; stroke: var(--text-soft); stroke-width: 1.4; }
  .address {
    position: absolute; right: 52px; bottom: 38px; text-align: right;
    color: var(--text-white); font-size: 16px; line-height: 1.45;
  }
  .back .brand { left: 50%; top: 70px; transform: translateX(-50%); font-size: 50px; }
  .back .brand-mark { width: 24px; height: 24px; }
</style>
</head>
<body>
<main class="sheet">
  <section class="card front">
    <svg class="card-waves" viewBox="0 0 700 400" aria-hidden="true">
      <path d="M0 0 H700 V250 C560 150 300 95 0 125 Z" fill="var(--brand-blue)"/>
      <path d="M0 125 C300 95 560 150 700 250 V272 C560 178 300 122 0 150 Z" fill="var(--swoosh-gray)"/>
    </svg>
    <div class="holder">
      <div class="holder-name">Martin Coles</div>
      <div class="holder-role">Senior Partner</div>
    </div>
    <div class="brand"><span class="brand-mark"></span>brightvale</div>
    <ul class="contacts">
      <li><svg viewBox="0 0 16 16"><path d="M3 1l3 3-2 2c1 2 4 5 6 6l2-2 3 3-2 2C7 15 1 9 1 3z"/></svg>1 877 555 0143</li>
      <li><svg viewBox="0 0 16 16"><path d="M4 0h8v16H4zM5.5 2v10h5V2z" fill-rule="evenodd"/></svg>1 519 555 0172</li>
      <li><svg viewBox="0 0 16 16"><path d="M4 0h6v5H4zM1 6h14v10H1zM3 9h4v2H3z" fill-rule="evenodd"/></svg>1 877 555 0144</li>
      <li><svg viewBox="0 0 16 16"><path d="M0 3h16v10H0zM1.5 4.5 8 9l6.5-4.5v-0.2H1.5z" fill-rule="evenodd"/></svg>name@brightvale.example</li>
      <li><svg class="globe" viewBox="0 0 16 16"><circle cx="8" cy="8" r="7"/><ellipse cx="8" cy="8" rx="3" ry="7"/><path d="M1 8h14"/></svg>www.brightvale.example</li>
    </ul>
    <div class="address">B12 9th floor Plaza<br>Harbour Lane Road WTN</div>
  </section>

  <section class="card back">
    <div class="brand"><span class="brand-mark"></span>brightvale</div>
  </section>
</main>
</body>
</html>
```